Company identity deisgn should support 2 languages

I would like to get our company identity design
This includes the following only
Business Cards 2 languages Arabic and English
Email signature
Letterhead
Linkedin profile images
Attached is the logo in Ai format

Requirements
Must have
• For business card
Must have
Name and Adrees in arabic
Name and Address in english
You might use both side of the card
Should not have
• Any pictures other than the logo

```html
<!DOCTYPE html>
<html lang="en">
<head>
<meta charset="utf-8">
<title>Northwind Cognitive Systems – Business Cards</title>
<link href="https://fonts.googleapis.com/css2?family=Poppins:wght@400;500;600&family=Noto+Kufi+Arabic:wght@500&family=Noto+Naskh+Arabic:wght@400&display=swap" rel="stylesheet">
<style>
  :root{
    --bg:#8a8a8a;
    --card:#ffffff;
    --blue:#1676c2;
    --ink:#3a3a3a;
    --muted:#8c8c8c;
    --rule:#cfcfcf;
  }
  *{margin:0;padding:0;box-sizing:border-box}
  html,body{width:1200px;height:1200px;overflow:hidden}
  body{background:var(--bg);font-family:"Poppins",sans-serif;position:relative}
  .card{position:absolute;left:240px;width:720px;height:410px;background:var(--card);border-radius:26px}
  .card--en{top:150px}
  .card--ar{top:640px}
  .brand{position:absolute;left:0;right:0;top:108px;display:flex;justify-content:center;align-items:center;gap:14px}
  .brand__dot{width:34px;height:34px;border-radius:50%;background:var(--blue)}
  .brand__name{font-family:"Poppins",sans-serif;font-weight:500;font-size:23px;letter-spacing:1px;color:var(--blue)}
  .rule{position:absolute;top:246px;left:37px;width:633px;height:1.5px;background:var(--rule)}
  .rule::before{content:"";position:absolute;left:0;top:-2px;width:207px;height:4px;background:var(--blue)}
  .person{position:absolute;left:42px;top:270px}
  .person__name{font-weight:600;font-size:24px;color:var(--blue);line-height:1.2;letter-spacing:.3px}
  .person__role{font-size:16px;color:var(--muted);line-height:1.3}
  .person__address{margin-top:10px;font-size:16.5px;color:var(--ink);line-height:1.35}
  .card--ar .person__name{font-family:"Noto Kufi Arabic",sans-serif;font-weight:500;font-size:21px;line-height:1.5}
  .card--ar .person__role{font-family:"Noto Kufi Arabic",sans-serif;font-size:15px;line-height:1.2}
  .card--ar .person__address{font-family:"Noto Naskh Arabic",serif;font-size:15px;line-height:1.75}
  .contact{position:absolute;right:42px;top:292px;list-style:none;text-align:right}
  .contact li{display:flex;justify-content:flex-end;align-items:center;gap:10px;font-size:17px;color:var(--ink);line-height:20.5px}
  .contact svg{width:15px;height:15px;flex:none;fill:var(--blue)}
</style>
</head>
<body>

<section class="card card--en" lang="en">
  <div class="brand"><span class="brand__dot"></span><span class="brand__name">NORTHWIND COGNITIVE SYSTEMS</span></div>
  <div class="rule"></div>
  <div class="person">
    <p class="person__name">DANIEL REYES</p>
    <p class="person__role">President</p>
    <p class="person__address">1420 Cedar Ridge Road<br>Fairbanks, Alaska 99701</p>
  </div>
  <ul class="contact">
    <li>555-214-7730<svg viewBox="0 0 16 16"><path d="M3.6 1.5l2.3 2.6-1.3 1.8c.9 2 2.5 3.6 4.5 4.5l1.8-1.3 2.6 2.3-1.2 2.1C7.4 13.4 2.6 8.6 1.5 2.7z"/></svg></li>
    <li>555-318-6042<svg viewBox="0 0 16 16"><path d="M4 1h8v14H4zM5.5 2.5v10h5v-10z"/></svg></li>
    <li>info@northwindcognitive.com<svg viewBox="0 0 16 16"><path d="M1 4h14v9H1zM2 5v.6l6 4 6-4V5z"/></svg></li>
    <li>www.northwindcognitive.com<svg viewBox="0 0 16 16"><circle cx="8" cy="8" r="7"/><path d="M4 6c1.5-1 2 1 3.5 0S8 3 10 4c-.5 2-2 2-2 4s2 1 2 3-2 2.5-3 2c0-2-2-2-2-4S3 8 4 6z" fill="#fff"/></svg></li>
  </ul>
</section>

<section class="card card--ar">
  <div class="brand"><span class="brand__dot"></span><span class="brand__name">NORTHWIND COGNITIVE SYSTEMS</span></div>
  <div class="rule"></div>
  <div class="person" lang="ar" dir="rtl" style="text-align:left">
    <p class="person__name">دانيال رييس</p>
    <p class="person__role">رئيس</p>
    <p class="person__address">1420 طريق سيدار ريدج<br>فيربانكس، ألاسكا 99701</p>
  </div>
  <ul class="contact" lang="en">
    <li>555-214-7730<svg viewBox="0 0 16 16"><path d="M3.6 1.5l2.3 2.6-1.3 1.8c.9 2 2.5 3.6 4.5 4.5l1.8-1.3 2.6 2.3-1.2 2.1C7.4 13.4 2.6 8.6 1.5 2.7z"/></svg></li>
    <li>555-318-6042<svg viewBox="0 0 16 16"><path d="M4 1h8v14H4zM5.5 2.5v10h5v-10z"/></svg></li>
    <li>info@northwindcognitive.com<svg viewBox="0 0 16 16"><path d="M1 4h14v9H1zM2 5v.6l6 4 6-4V5z"/></svg></li>
    <li>www.northwindcognitive.com<svg viewBox="0 0 16 16"><circle cx="8" cy="8" r="7"/><path d="M4 6c1.5-1 2 1 3.5 0S8 3 10 4c-.5 2-2 2-2 4s2 1 2 3-2 2.5-3 2c0-2-2-2-2-4S3 8 4 6z" fill="#fff"/></svg></li>
  </ul>
</section>

</body>
</html>
```